Firm Stationery Design

I need a design for stationery, including: Stationery First Page, Stationery Second Sheet, Envelope, Mailing Label for Flat Envelopes, and Business Cards

```html
<!DOCTYPE html>
<html lang="en">
<head>
<meta charset="utf-8">
<title>Harlow Law LLC — Stationery</title>
<link href="https://fonts.googleapis.com/css2?family=Montserrat:wght@800&family=Arimo:wght@400;700&display=swap" rel="stylesheet">
<style>
  :root{
    --backdrop:#c9c9c9;
    --ink:#333333;
    --orange:#f89c0e;
    --paper:#ffffff;
    --text:#555555;
    --body:#6a6a6a;
    --faint:#f0f0f0;
    --line:#9a9a9a;
  }
  *{box-sizing:border-box;margin:0;padding:0}
  html,body{width:1200px;height:1022px;overflow:hidden;background:var(--backdrop)}
  body{position:relative;font-family:"Arimo",Arial,sans-serif;color:var(--text)}
  .piece{position:absolute;background:var(--paper);box-shadow:2px 3px 5px rgba(0,0,0,.28);overflow:hidden}
  .abs{position:absolute}

  .brand{position:absolute;display:flex;flex-direction:column;align-items:center;font-family:"Montserrat",Arial,sans-serif;font-weight:800;color:var(--ink);line-height:1}
  .brand-mark{background:var(--orange);margin-bottom:var(--gap,4px)}
  .brand-sub{letter-spacing:.5em;margin-right:-.5em;margin-top:var(--subgap,3px)}
  .brand.on-dark{color:#fff}

  .contact-block{position:absolute;border-left:.6px solid var(--line);line-height:1.45}
  .contact-block .row{display:flex;align-items:center;white-space:nowrap}
  .icon{fill:var(--orange);flex:none}

  .faint-block{position:absolute;background:var(--faint)}

  .card-front{left:40px;top:94px;width:338px;height:193px}
  .card-front .divider{left:169px;top:48px;width:1px;height:97px;background:var(--line)}
  .card-front .details{left:182px;top:46px;font-size:10px;line-height:1.25;color:var(--text)}
  .card-front .person{font-weight:700;font-size:12.5px;color:var(--orange);line-height:1}
  .card-front .role{margin-top:2px}
  .card-front .address{margin-top:7px}
  .card-front .contacts{margin-top:9px}
  .card-front .contacts .row{display:flex;align-items:center;gap:3px}

  .card-back{left:40px;top:310px;width:338px;height:193px;background:var(--ink)}

  .letterhead{left:401px;top:94px;width:292px;height:413px}
  .letter-body{position:absolute;left:26px;top:128px;width:240px;color:var(--body)}
  .greeting{font-size:6.5px;color:var(--text);margin-bottom:11px}
  .letter-body p{font-size:4.9px;line-height:6px;margin-bottom:5.5px;text-align:left}
  .sign-off{font-size:3.6px;margin-top:10px}
  .signature{width:36px;height:10px;margin-top:10px;background:linear-gradient(90deg,#d8d8d8,#eeeeee);border-radius:2px}

  .envelope-front{left:714px;top:94px;width:446px;height:193px}
  .envelope-front .return{left:13px;top:55px;font-size:6.5px;line-height:1.25;color:var(--text)}

  .envelope-back{left:714px;top:311px;width:446px;height:194px}

  .folder-closed{left:40px;top:532px;width:546px;height:386px}
  .folder-closed .cover{left:0;top:0;width:273px;height:386px;background:var(--ink)}
  .folder-closed .inner{left:273px;top:0;width:273px;height:386px;background:linear-gradient(90deg,#e2e2e4 0%,#f7f7f7 45%,#ffffff 100%)}

  .folder-open{left:622px;top:532px;width:538px;height:386px;background:linear-gradient(90deg,#ffffff 0%,#efeff0 40%,#d6d6d8 50%,#c4c5c8 52%,#dadbdd 100%)}
  .folder-open .left-panel{left:0;top:0;width:269px;height:386px;background:linear-gradient(90deg,#ffffff 0%,#ededee 60%,#d4d4d6 100%)}
  .folder-open .sheet{left:281px;top:15px;width:246px;height:300px;background:linear-gradient(90deg,#fff 0%,#f6f6f6 100%)}
  .sheet .letter-body{left:22px;top:110px;width:200px}
  .sheet .greeting{font-size:5px;margin-bottom:8px}
  .sheet .letter-body p{font-size:3.9px;line-height:4.9px;margin-bottom:5px}
  .folder-open .pockets{position:absolute;left:0;top:0}
</style>
</head>
<body>
<svg width="0" height="0" style="position:absolute">
  <defs>
    <symbol id="i-phone" viewBox="0 0 10 10"><path d="M1 3.5C1 2.5 2 2 5 2s4 .5 4 1.5V4.5H7V3.6H3v.9H1z M2 5h6l1 3.5H1z"/></symbol>
    <symbol id="i-mail" viewBox="0 0 10 10"><path d="M1 4.5 5 1.5 9 4.5V9H1z"/><path d="M1.6 5 5 7.2 8.4 5" stroke="#fff" stroke-width=".7" fill="none"/></symbol>
    <symbol id="i-web" viewBox="0 0 10 10"><circle cx="5" cy="5" r="4.3"/><path d="M3 3.2 5 4.2 4 6.5 6.2 7.4M6.5 2.4 7.4 4.2" stroke="#fff" stroke-width=".7" fill="none"/></symbol>
  </defs>
</svg>

<!-- Business card: front -->
<section class="piece card-front">
  <div class="brand" style="left:67px;top:48px;font-size:20px;--gap:7px">
    <div class="brand-mark" style="width:34px;height:34px"></div>
    <div class="brand-name">HARLOW</div>
    <div class="brand-sub" style="font-size:8px;--subgap:6px">LAW LLC</div>
  </div>
  <div class="abs divider"></div>
  <div class="abs details">
    <div class="person">DANIEL WHITFORD</div>
    <div class="role">Manager</div>
    <div class="address">Your Address, City<br>State, Zip 0000</div>
    <div class="contacts">
      <div class="row"><svg class="icon" width="9" height="9"><use href="#i-phone"/></svg>555-014-7382</div>
      <div class="row"><svg class="icon" width="9" height="9"><use href="#i-mail"/></svg>youremail@mailbox.com</div>
      <div class="row"><svg class="icon" width="9" height="9"><use href="#i-web"/></svg>www.yourwebsite.com</div>
    </div>
  </div>
</section>

<!-- Business card: back -->
<section class="piece card-back">
  <div class="brand on-dark" style="left:91px;top:36px;width:156px;font-size:27px;--gap:12px">
    <div class="brand-mark" style="width:58px;height:58px"></div>
    <div class="brand-name">HARLOW</div>
    <div class="brand-sub" style="font-size:10px;--subgap:10px">LAW LLC</div>
  </div>
</section>

<!-- Letterhead -->
<section class="piece letterhead">
  <div class="brand" style="left:26px;top:15px;font-size:8.5px;--gap:3px">
    <div class="brand-mark" style="width:14px;height:14px"></div>
    <div class="brand-name">HARLOW</div>
    <div class="brand-sub" style="font-size:3.4px;--subgap:3px">LAW LLC</div>
  </div>
  <div class="contact-block" style="left:219px;top:18px;padding-left:4px;font-size:4.4px">
    <div>Your Address, City</div>
    <div style="margin-bottom:2px">State, Zip 0000</div>
    <div class="row"><svg class="icon" width="4" height="4"><use href="#i-phone"/></svg>&nbsp;555-014-7382</div>
    <div class="row"><svg class="icon" width="4" height="4"><use href="#i-mail"/></svg>&nbsp;youremail@mailbox.com</div>
    <div class="row"><svg class="icon" width="4" height="4"><use href="#i-web"/></svg>&nbsp;www.yourwebsite.com</div>
  </div>
  <div class="faint-block" style="left:133px;top:262px;width:159px;height:151px"></div>
  <div class="letter-body">
    <div class="greeting">Dear Mr. Whitford,</div>
    <p>Lorem ipsum dolor sit amet, consectetuer adipiscing elit, sed diam nonummy nibh euismod tincidunt ut laoreet dolore magna aliquam erat volutpat. Ut wisi enim ad minim veniam, quis nostrud exerci tation ullamcorper suscipit lobortis nisl ut aliquip ex ea commodo consequat. Duis autem vel eum iriure dolor in hendrerit in vulputate velit esse molestie consequat.</p>
    <p>Lorem ipsum dolor sit amet, consectetuer adipiscing elit, sed diam nonummy nibh euismod tincidunt ut laoreet dolore magna aliquam erat volutpat. Ut wisi enim ad minim veniam, quis nostrud exerci tation ullamcorper suscipit lobortis nisl ut aliquip ex ea commodo consequat. Duis autem vel eum iriure dolor in hendrerit in vulputate velit esse molestie consequat.</p>
    <p>Lorem ipsum dolor sit amet, consectetuer adipiscing elit, sed diam nonummy nibh euismod tincidunt ut laoreet dolore magna aliquam erat volutpat. Ut wisi enim ad minim veniam, quis nostrud exerci tation ullamcorper suscipit lobortis nisl ut aliquip ex ea commodo consequat. Duis autem vel eum iriure dolor in hendrerit in vulputate velit esse molestie consequat.</p>
    <p>Lorem ipsum dolor sit amet, consectetuer adipiscing elit, sed diam nonummy nibh euismod tincidunt ut laoreet dolore magna aliquam erat volutpat. Ut wisi enim ad minim veniam, quis nostrud exerci tation ullamcorper suscipit lobortis nisl ut aliquip ex ea commodo consequat. Duis autem vel eum iriure dolor in hendrerit in vulputate velit esse molestie consequat.</p>
    <div class="sign-off">Sincerely,</div>
    <div class="signature" role="img" aria-label="Handwritten signature"></div>
  </div>
</section>

<!-- Envelope: front -->
<section class="piece envelope-front">
  <div class="brand" style="left:13px;top:12px;font-size:8.5px;--gap:3px">
    <div class="brand-mark" style="width:14px;height:14px"></div>
    <div class="brand-name">HARLOW</div>
    <div class="brand-sub" style="font-size:3.4px;--subgap:3px">LAW LLC</div>
  </div>
  <div class="abs return">Your Address, City<br>State, Zip 0000</div>
  <div class="faint-block" style="left:277px;top:33px;width:169px;height:160px"></div>
</section>

<!-- Envelope: back -->
<section class="piece envelope-back">
  <svg class="abs" style="left:0;top:0" width="446" height="194" viewBox="0 0 446 194">
    <defs>
      <filter id="flap-shadow" x="-5%" y="-20%" width="110%" height="160%">
        <feDropShadow dx="0" dy="2" stdDeviation="2" flood-color="#000" flood-opacity=".25"/>
      </filter>
    </defs>
    <path d="M4 2 Q8 40 20 47 Q26 53 40 53 H406 Q420 53 426 47 Q438 40 442 2 Z" fill="#fff" filter="url(#flap-shadow)"/>
  </svg>
  <div class="brand" style="left:199px;top:9px;font-size:8px;--gap:3px">
    <div class="brand-mark" style="width:13px;height:13px"></div>
    <div class="brand-name">HARLOW</div>
    <div class="brand-sub" style="font-size:3.2px;--subgap:3px">LAW LLC</div>
  </div>
</section>

<!-- Presentation folder: closed -->
<section class="piece folder-closed">
  <div class="abs cover">
    <div class="brand on-dark" style="left:50px;top:122px;width:173px;font-size:32px;--gap:16px">
      <div class="brand-mark" style="width:72px;height:72px"></div>
      <div class="brand-name">HARLOW</div>
      <div class="brand-sub" style="font-size:12px;--subgap:12px">LAW LLC</div>
    </div>
  </div>
  <div class="abs inner">
    <div class="brand" style="left:22px;top:16px;font-size:8px;--gap:3px">
      <div class="brand-mark" style="width:13px;height:13px"></div>
      <div class="brand-name">HARLOW</div>
      <div class="brand-sub" style="font-size:3.2px;--subgap:3px">LAW LLC</div>
    </div>
    <div class="contact-block" style="left:205px;top:18px;padding-left:4px;font-size:4.2px">
      <div>Your Address, City</div>
      <div style="margin-bottom:2px">State, Zip 0000</div>
      <div class="row"><svg class="icon" width="4" height="4"><use href="#i-phone"/></svg>&nbsp;555-014-7382</div>
      <div class="row"><svg class="icon" width="4" height="4"><use href="#i-mail"/></svg>&nbsp;youremail@mailbox.com</div>
      <div class="row"><svg class="icon" width="4" height="4"><use href="#i-web"/></svg>&nbsp;www.yourwebsite.com</div>
    </div>
    <div class="faint-block" style="left:125px;top:245px;width:148px;height:141px"></div>
  </div>
</section>

<!-- Presentation folder: open -->
<section class="piece folder-open">
  <div class="abs left-panel"></div>
  <div class="abs sheet">
    <div class="brand" style="left:23px;top:13px;font-size:7.5px;--gap:3px">
      <div class="brand-mark" style="width:12px;height:12px"></div>
      <div class="brand-name">HARLOW</div>
      <div class="brand-sub" style="font-size:3px;--subgap:3px">LAW LLC</div>
    </div>
    <div class="contact-block" style="left:185px;top:17px;padding-left:3px;font-size:3.4px">
      <div>Your Address, City</div>
      <div style="margin-bottom:1.5px">State, Zip 0000</div>
      <div class="row"><svg class="icon" width="3.4" height="3.4"><use href="#i-phone"/></svg>&nbsp;555-014-7382</div>
      <div class="row"><svg class="icon" width="3.4" height="3.4"><use href="#i-mail"/></svg>&nbsp;youremail@mailbox.com</div>
      <div class="row"><svg class="icon" width="3.4" height="3.4"><use href="#i-web"/></svg>&nbsp;www.yourwebsite.com</div>
    </div>
    <div class="faint-block" style="left:112px;top:219px;width:134px;height:81px"></div>
    <div class="letter-body">
      <div class="greeting">Dear Mr. Whitford,</div>
      <p>Lorem ipsum dolor sit amet, consectetuer adipiscing elit, sed diam nonummy nibh euismod tincidunt ut laoreet dolore magna aliquam erat volutpat. Ut wisi enim ad minim veniam, quis nostrud exerci tation ullamcorper suscipit lobortis nisl ut aliquip ex ea commodo consequat. Duis autem vel eum iriure dolor in hendrerit in vulputate velit esse molestie consequat.</p>
      <p>Lorem ipsum dolor sit amet, consectetuer adipiscing elit, sed diam nonummy nibh euismod tincidunt ut laoreet dolore magna aliquam erat volutpat. Ut wisi enim ad minim veniam, quis nostrud exerci tation ullamcorper suscipit lobortis nisl ut aliquip ex ea commodo consequat. Duis autem vel eum iriure dolor in hendrerit in vulputate velit esse molestie consequat.</p>
      <p>Lorem ipsum dolor sit amet, consectetuer adipiscing elit, sed diam nonummy nibh euismod tincidunt ut laoreet dolore magna aliquam erat volutpat. Ut wisi enim ad minim veniam, quis nostrud exerci tation ullamcorper suscipit lobortis nisl ut aliquip ex ea commodo consequat. Duis autem vel eum iriure dolor in hendrerit in vulputate velit esse molestie consequat.</p>
      <p>Lorem ipsum dolor sit amet, consectetuer adipiscing elit, sed diam nonummy nibh euismod tincidunt ut laoreet dolore magna aliquam erat volutpat. Ut wisi enim ad minim veniam, quis nostrud exerci tation ullamcorper suscipit lobortis nisl ut aliquip ex ea commodo consequat. Duis autem vel eum iriure dolor in hendrerit in vulputate velit esse molestie consequat.</p>
      <div class="sign-off" style="font-size:3px;margin-top:4px">Sincerely,</div>
    </div>
  </div>
  <svg class="pockets" width="538" height="386" viewBox="0 0 538 386">
    <path d="M0 247 H244 Q252 247 253 256 L269 386 H0 Z" fill="var(--ink)"/>
    <path d="M269 386 L287 256 Q289 247 298 247 H538 V386 Z" fill="var(--ink)"/>
  </svg>
</section>
</body>
</html>
```